Business card design for holistic health care clinic

We need a double-sided business card design for our holistic health care clinic that integrates our logo design and also its color scheme. My business is called Valmira. It is an integrative medicine clinic. You have already done the logo for me. Please ensure an elegant and upscale design that is not cluttered, but still has all the necessary information (please see below for details).

Target Market(s)

Wellness, fitness, rehabilitation for educated, well-traveled open-minded clients who are focused on natural, organic, balanced and preventive healthcare and lifestyle.

Industry/Entity Type

Medical

Contact Information for Business Card

Modern, clean.

Number of Pages Required

1 page

Font styles to use
Serif
Sans Serif

Colors

Designer to choose colors to be used in the design.

Requirements
Must have
• Logo on one side, all other information on the other side.
• Other information should include:
• Tobias Wrenfeld - DOE, CPT, LMT
• 4100 East Marrow Drive
• Austin, TX 78119
• 512 555 0148
• 818 555 0192
• info@ValmiraHealth.example
• t.wrenfeld@ValmiraHealth.example
Nice to have
• Darker background on front - but not totally black - shaded/dark gray.

```html
<!DOCTYPE html>
<html lang="en">
<head>
<meta charset="utf-8">
<title>Valmira — Business Card</title>
<link rel="stylesheet" href="https://fonts.googleapis.com/css2?family=Nunito:wght@800&family=Quicksand:wght@400;500;700&display=swap">
<style>
  :root {
    --stage: #3a3531;
    --card: #232228;
    --card-edge: #1a191e;
    --accent: #1b8fd2;
    --accent-soft: #1677b0;
  }
  * { box-sizing: border-box; margin: 0; padding: 0; }
  html, body { width: 1200px; height: 780px; overflow: hidden; }
  body {
    background: var(--stage);
    font-family: "Quicksand", sans-serif;
    color: var(--accent);
    position: relative;
  }
  .card {
    position: absolute;
    top: 235px;
    width: 540px;
    height: 309px;
    background: var(--card);
    border: 1px solid var(--card-edge);
    box-shadow: 0 10px 30px rgba(0,0,0,.45);
  }
  .card--front { left: 40px; }
  .card--back { left: 620px; }

  .brand { position: absolute; text-align: center; }
  .brand__name {
    font-family: "Nunito", sans-serif;
    font-weight: 800;
    letter-spacing: 1px;
    color: var(--accent);
    line-height: 1;
    text-transform: uppercase;
  }
  .brand__tagline {
    font-family: "Quicksand", sans-serif;
    font-weight: 700;
    color: var(--accent);
    white-space: nowrap;
  }
  .card--front .brand { left: 0; right: 0; top: 108px; }
  .card--front .brand__name { font-size: 58px; }
  .card--front .brand__tagline { font-size: 15px; margin-top: 6px; }

  .card--back .brand { right: 28px; top: 38px; }
  .card--back .brand__name { font-size: 44px; }
  .card--back .brand__tagline { font-size: 11.5px; margin-top: 4px; }

  .holder { position: absolute; left: 0; top: 112px; display: flex; align-items: center; }
  .holder__lead { width: 36px; margin-right: 10px; }
  .holder__name {
    font-weight: 700;
    font-size: 23px;
    letter-spacing: .5px;
    text-transform: uppercase;
    white-space: nowrap;
  }
  .holder__trail { width: 270px; margin-left: 12px; }
  .holder__cred {
    position: absolute;
    left: 46px;
    top: 144px;
    font-size: 12px;
    letter-spacing: .5px;
    color: var(--accent-soft);
  }

  .contact {
    position: absolute;
    left: 26px;
    right: 20px;
    bottom: 34px;
    display: flex;
    align-items: stretch;
    font-size: 12.5px;
    font-weight: 500;
  }
  .contact__group { display: flex; flex-direction: column; gap: 6px; padding: 0 12px; }
  .contact__group:first-child { padding-left: 0; }
  .contact__group + .contact__group { border-left: 1px solid var(--accent); }
  .contact__item { display: flex; align-items: center; gap: 6px; white-space: nowrap; }
  .icon { width: 13px; height: 13px; flex: none; }
</style>
</head>
<body>

  <section class="card card--front" aria-label="Card front">
    <div class="brand">
      <div class="brand__name">Valmira</div>
      <div class="brand__tagline">Integrative Holistic Medicine</div>
    </div>
  </section>

  <section class="card card--back" aria-label="Card back">
    <div class="brand">
      <div class="brand__name">Valmira</div>
      <div class="brand__tagline">Integrative Holistic Medicine</div>
    </div>

    <div class="holder">
      <svg class="holder__lead" viewBox="0 0 36 14" aria-hidden="true">
        <g stroke="#1b8fd2" stroke-width="1.4"><line x1="0" y1="2" x2="36" y2="2"/><line x1="0" y1="7" x2="36" y2="7"/><line x1="0" y1="12" x2="36" y2="12"/></g>
      </svg>
      <span class="holder__name">Tobias Wrenfeld</span>
      <svg class="holder__trail" viewBox="0 0 270 14" aria-hidden="true">
        <g stroke="#1b8fd2" stroke-width="1.4"><line x1="0" y1="2" x2="270" y2="2"/><line x1="0" y1="7" x2="270" y2="7"/><line x1="0" y1="12" x2="270" y2="12"/></g>
      </svg>
    </div>
    <div class="holder__cred">DOE, CPT, LMT</div>

    <div class="contact">
      <div class="contact__group">
        <div class="contact__item">
          <svg class="icon" viewBox="0 0 14 14" aria-hidden="true"><circle cx="7" cy="7" r="6.2" fill="none" stroke="#1b8fd2"/><rect x="4.6" y="3.4" width="4.8" height="7.2" rx="1" fill="none" stroke="#1b8fd2"/></svg>
          <span>512 555 0148</span>
        </div>
        <div class="contact__item">
          <svg class="icon" viewBox="0 0 14 14" aria-hidden="true"><circle cx="7" cy="7" r="6.2" fill="none" stroke="#1b8fd2"/><path d="M4.6 3.8c.5-.4 1-.3 1.3.2l.5.9c.2.4 0 .7-.3 1 .4.8 1 1.4 1.8 1.8.3-.3.6-.5 1-.3l.9.5c.5.3.6.8.2 1.3-1.6 1.6-6.8-3.4-5.4-5.4z" fill="#1b8fd2"/></svg>
          <span>818 555 0192</span>
        </div>
      </div>
      <div class="contact__group">
        <div class="contact__item">
          <svg class="icon" viewBox="0 0 14 14" aria-hidden="true"><circle cx="7" cy="7" r="6.2" fill="none" stroke="#1b8fd2"/><rect x="3.6" y="4.6" width="6.8" height="4.8" fill="none" stroke="#1b8fd2"/><path d="M3.6 4.6 7 7.4l3.4-2.8" fill="none" stroke="#1b8fd2"/></svg>
          <span>info@ValmiraHealth.example</span>
        </div>
        <div class="contact__item">
          <svg class="icon" viewBox="0 0 14 14" aria-hidden="true"><circle cx="7" cy="7" r="6.2" fill="none" stroke="#1b8fd2"/><rect x="3.6" y="4.6" width="6.8" height="4.8" fill="none" stroke="#1b8fd2"/><path d="M3.6 4.6 7 7.4l3.4-2.8" fill="none" stroke="#1b8fd2"/></svg>
          <span>t.wrenfeld@ValmiraHealth.example</span>
        </div>
      </div>
      <div class="contact__group">
        <div class="contact__item"><span>4100 East Marrow Drive</span></div>
        <div class="contact__item"><span>Austin, TX 78119</span></div>
      </div>
    </div>
  </section>

</body>
</html>
```